Brindle Healthcare Coming Soon Sign

I need a large (10 x5) road banner announcing the construction of our new medical practice at 5187 Larkmoor Road in John's Island. The name of our practice is Brindle Healthcare and we thought it would be fund to nick name it the "Brindle Waystation". We'd like the tagline to read - "There's nothing healthy about driving an hour to see your doctor. So we're coming to you." Opening Late 2025 I have attached three logos as we have two other practices (Brindle Urgent and Brindle Aesthetics ) that should be present on the bottom of the sign but the main business is Brindle Healthcare. For more information on our look/feel visit our website www.goplainway-example.com (which should be somewhere on the banner as well)
Updates

The signage needs to say Coming Late Fall 2025!

Target Market(s)

Drive By traffic must be made aware that we are coming soon

Industry/Entity Type

Healthcare

Requirements
Nice to have
• Western Theme

```html
<!DOCTYPE html>
<html lang="en">
<head>
<meta charset="utf-8">
<title>Brindle Waystation – Coming Late Fall 2025</title>
<link rel="stylesheet" href="https://fonts.googleapis.com/css2?family=Alfa+Slab+One&family=Oswald:wght@600&family=Montserrat:wght@600&display=swap">
<style>
  :root {
    --page: #ffffff;
    --boards: #e6e6e4;
    --board-seam: #c9c9c6;
    --trim: #6e4633;
    --trim-seam: #4a2c1f;
    --navy: #13305f;
    --navy-deep: #0f2a57;
    --brown-ink: #2f1b16;
    --ribbon: #0aa6d6;
    --white: #ffffff;
    --pink: #e6237a;
    --red: #ef4136;
    --teal: #2aa7d9;
  }
  * { box-sizing: border-box; margin: 0; padding: 0; }
  html, body { width: 1041px; height: 1200px; overflow: hidden; background: var(--page); }
  .canvas { position: relative; width: 1041px; height: 1200px; }

  .banner {
    position: absolute; left: 20px; top: 350px;
    width: 1001px; height: 500px; overflow: hidden;
    background:
      repeating-linear-gradient(90deg, transparent 0 58px, var(--board-seam) 58px 60px),
      var(--boards);
  }
  .banner__lower {
    position: absolute; left: 0; top: 310px; width: 100%; height: 190px;
    background:
      repeating-linear-gradient(90deg, transparent 0 58px, rgba(0,0,0,.12) 58px 60px),
      var(--navy);
  }
  .banner__trim {
    position: absolute; left: 0; top: 0; width: 100%; height: 25px;
    background:
      repeating-linear-gradient(90deg, var(--trim) 0 12px, var(--trim-seam) 12px 14px);
    border-bottom: 2px solid var(--trim-seam);
  }

  .brand {
    position: absolute; left: 36px; top: 60px; width: 120px;
    display: flex; flex-direction: column; align-items: center; gap: 6px;
  }
  .brand__mark { width: 26px; height: 26px; background: var(--teal); }
  .brand__name {
    font-family: "Montserrat", sans-serif; font-weight: 600;
    font-size: 15px; letter-spacing: 2px; color: var(--navy-deep);
    text-align: center; text-transform: uppercase; line-height: 1.15;
  }

  .headline { font-family: "Alfa Slab One", serif; }
  .headline__line {
    position: absolute; white-space: nowrap; text-align: center; line-height: 1;
    transform: translateX(-50%);
  }
  .headline__name { left: 524px; top: 56px; font-size: 58px; color: var(--brown-ink); font-weight: 400; }
  .headline__date { left: 503px; top: 136px; font-size: 64px; color: var(--navy-deep); }
  .headline__tagline {
    left: 524px; top: 222px; font-size: 20px; line-height: 31px; color: var(--brown-ink);
  }

  .photo { position: absolute; }
  .photo--hat {
    left: 0; top: 255px; width: 225px; height: 245px;
    background: radial-gradient(ellipse at 55% 40%, #7a4d35 0%, #5a3524 45%, #8a5433 80%, #6a3a20 100%);
    border-radius: 0 60px 0 0;
  }
  .photo--wagon {
    left: 738px; top: 319px; width: 263px; height: 181px;
    background: radial-gradient(ellipse at 55% 50%, #8a7058 0%, #6b5440 55%, rgba(80,60,45,.7) 100%);
    border-radius: 40px 0 0 0;
  }

  .ribbon { position: absolute; left: 316px; top: 357px; width: 370px; height: 52px; }
  .ribbon svg { position: absolute; inset: 0; }
  .ribbon__url {
    position: absolute; inset: 0; display: flex; align-items: center; justify-content: center;
    font-family: "Oswald", sans-serif; font-weight: 600; font-size: 22px;
    color: var(--brown-ink); white-space: nowrap;
  }

  .partners {
    position: absolute; left: 318px; top: 437px; width: 370px;
    display: flex; justify-content: space-between; align-items: center;
  }
  .partner { display: flex; align-items: center; gap: 8px; }
  .partner__mark { width: 22px; height: 22px; }
  .partner__mark--aesthetics { background: var(--pink); border-radius: 50%; }
  .partner__mark--urgent { background: var(--red); }
  .partner__name {
    font-family: "Montserrat", sans-serif; font-weight: 600; font-size: 14px;
    letter-spacing: 1.5px; line-height: 1.25; text-transform: uppercase; color: var(--white);
  }
</style>
</head>
<body>
<div class="canvas">
  <section class="banner">
    <div class="banner__lower">
      <div class="banner__trim"></div>
    </div>

    <div class="brand">
      <div class="brand__mark"></div>
      <div class="brand__name">Brindle Healthcare</div>
    </div>

    <div class="headline">
      <h1 class="headline__line headline__name">Brindle Waystation</h1>
      <p class="headline__line headline__date">Coming Late Fall 2025!</p>
      <p class="headline__line headline__tagline">Conserving Rural John's Island<br>with Home Grown Progressive Primary Care</p>
    </div>

    <div class="photo photo--hat" role="img" aria-label="Leather cowboy hat and coiled rope hanging on a wooden chair"></div>
    <div class="photo photo--wagon" role="img" aria-label="Old weathered wooden wagon with spoked wheels"></div>

    <div class="ribbon">
      <svg viewBox="0 0 370 52" preserveAspectRatio="none" aria-hidden="true">
        <polygon points="0,0 370,0 346,26 370,52 0,52 24,26" fill="var(--ribbon)"/>
      </svg>
      <span class="ribbon__url">WWW.GOPLAINWAY-EXAMPLE.COM</span>
    </div>

    <div class="partners">
      <div class="partner">
        <span class="partner__mark partner__mark--aesthetics"></span>
        <span class="partner__name">Brindle<br>Aesthetics</span>
      </div>
      <div class="partner">
        <span class="partner__mark partner__mark--urgent"></span>
        <span class="partner__name">Brindle<br>Urgent</span>
      </div>
    </div>
  </section>
</div>
</body>
</html>
```